Coastline Premier Retreats Business Card Design

Design a business card for Coastline Premier Retreats. Look at the website for colors and reference. Card should have logo, name, title, office number, mobile number, email, URL and a tagline like, "Luxury Hotel & Resort Email Marketing" (This might change).

https://www.coastlinepremierretreats.example

The rest I will leave up to your imagination.

Contact Information for Business Card

Logo, name, title, office number, mobile number, email, URL and a tagline like, "Luxury Hotel & Resort Email Marketing" (This might change).

```html
<!DOCTYPE html>
<html lang="en">
<head>
<meta charset="utf-8">
<title>Coastline Premier Retreats – Business Card</title>
<link rel="stylesheet" href="https://fonts.googleapis.com/css2?family=Open+Sans:wght@400;600;700&display=swap">
<style>
  :root {
    --backdrop: #232323;
    --card: #1f1f23;
    --card-emboss: #29292e;
    --accent: #f37321;
    --ink: #ffffff;
    --ink-soft: #e6e6e6;
  }
  * { box-sizing: border-box; margin: 0; padding: 0; }
  html, body {
    width: 1200px; height: 780px; overflow: hidden;
    background: var(--backdrop);
    font-family: "Open Sans", sans-serif;
  }
  .stage {
    position: relative; width: 1200px; height: 780px;
    display: flex; align-items: center; justify-content: center; gap: 40px;
  }
  .card {
    position: relative; width: 540px; height: 309px;
    background: var(--card);
    box-shadow: 0 18px 40px rgba(0,0,0,.45);
    overflow: hidden;
  }
  .card-front .swoosh { position: absolute; inset: 0; width: 100%; height: 100%; }
  .brand {
    position: absolute; left: 32px; top: 62px;
    display: flex; align-items: center; gap: 10px;
  }
  .brand-square {
    width: 14px; height: 14px; background: var(--accent); flex: none;
  }
  .brand-name {
    color: var(--ink); font-weight: 700; font-size: 15px;
    line-height: 1.15; letter-spacing: .03em; text-transform: uppercase;
    white-space: nowrap;
  }
  .divider {
    position: absolute; left: 252px; top: 78px; width: 1px; height: 140px;
    background: linear-gradient(to bottom, transparent, var(--ink) 50%, transparent);
  }
  .person { position: absolute; left: 268px; top: 88px; right: 16px; }
  .person-name {
    font-size: 24px; font-weight: 700; color: var(--ink); line-height: 1.1;
    white-space: nowrap;
  }
  .person-name .given { color: var(--accent); }
  .person-title { font-size: 13px; color: var(--ink-soft); margin-top: 2px; }
  .contacts { list-style: none; margin-top: 10px; }
  .contacts li {
    display: flex; align-items: center; gap: 7px;
    font-size: 11px; color: var(--ink); line-height: 18px;
    white-space: nowrap;
  }
  .contacts svg { width: 11px; height: 11px; flex: none; }
  .tagline {
    position: absolute; left: 0; right: 0; bottom: 16px;
    text-align: center; padding-right: 40px;
    font-size: 13px; color: var(--ink);
  }
  .card-back { display: flex; align-items: center; justify-content: center; }
  .back-name {
    color: var(--card-emboss); font-weight: 700; font-size: 30px;
    letter-spacing: .05em; text-transform: uppercase; text-align: center;
    line-height: 1.15;
    text-shadow: 0 1px 0 rgba(255,255,255,.04);
  }
</style>
</head>
<body>
<main class="stage">
  <section class="card card-front" aria-label="Business card front">
    <svg class="swoosh" viewBox="0 0 540 309" preserveAspectRatio="none" aria-hidden="true">
      <path d="M0,309 C130,200 380,208 540,309 Z" fill="#ffffff"/>
      <path d="M0,309 C130,210 372,216 530,309 Z" fill="var(--accent)"/>
    </svg>
    <div class="brand">
      <span class="brand-square"></span>
      <span class="brand-name">Coastline<br>Premier Retreats</span>
    </div>
    <span class="divider"></span>
    <div class="person">
      <h1 class="person-name"><span class="given">Daria</span> Holmwood</h1>
      <p class="person-title">Co-Founder</p>
      <ul class="contacts">
        <li><svg viewBox="0 0 12 12"><path d="M2 1h3l1 3-1.5 1a6 6 0 0 0 2.5 2.5L8 6l3 1v3c0 .6-.4 1-1 1A9 9 0 0 1 1 2c0-.6.4-1 1-1z" fill="var(--accent)"/></svg>(555) 214-3087</li>
        <li><svg viewBox="0 0 12 12"><rect x="3" y="1" width="6" height="10" rx="1" fill="none" stroke="var(--accent)" stroke-width="1.3"/></svg>(555) 360-1142</li>
        <li><svg viewBox="0 0 12 12"><circle cx="6" cy="6" r="5" fill="none" stroke="var(--accent)" stroke-width="1.3"/><path d="M1 6h10M6 1c2 2 2 8 0 10M6 1c-2 2-2 8 0 10" fill="none" stroke="var(--accent)" stroke-width="1"/></svg>www.coastlinepremierretreats.example</li>
        <li><svg viewBox="0 0 12 12"><rect x="1" y="2.5" width="10" height="7" fill="var(--accent)"/><path d="M1 2.5l5 4 5-4" fill="none" stroke="var(--card)" stroke-width="1"/></svg>info@coastlinepremierretreats.example</li>
      </ul>
    </div>
    <p class="tagline">Luxury Hotel &amp; Resort Email Marketing</p>
  </section>
  <section class="card card-back" aria-label="Business card back">
    <p class="back-name">Coastline<br>Premier Retreats</p>
  </section>
</main>
</body>
</html>
```